Business Card Design

We provide services doing multiple jobs in the construction industry.Please note: The company name needs to be ROCK SOLID BUILDING SERVICESAttached logo was an example of what we wanted. Can you change up the colors?

Industry/Entity Type

Construction

Contact Information for Business Card

ROCK SOLID BUILDING SERVICES5401 HUDSON BEND RDAUSTIN, TX 78734(512)243-6854ROCKSOLIDBUILDINGSERVICES@GMAIL.COM

```html
<!DOCTYPE html>
<html lang="en">
<head>
<meta charset="utf-8">
<title>Pearlwood Framing Works – Business Card</title>
<link rel="stylesheet" href="https://fonts.googleapis.com/css2?family=Exo+2:wght@400;600;700&display=swap">
<style>
  :root {
    --bg: #e7e4df;
    --card-white: #f4f4f5;
    --silver-light: #d9dadc;
    --silver-dark: #6d6e72;
    --navy: #1f2163;
    --navy-deep: #141650;
    --charcoal: #23242c;
    --ink: #1c1f5a;
    --text-light: #ffffff;
    --accent: #3b8fc4;
  }
  * { margin: 0; padding: 0; box-sizing: border-box; }
  html, body {
    width: 1200px; height: 828px; overflow: hidden;
    background: var(--bg);
    font-family: "Exo 2", sans-serif;
  }
  .canvas {
    width: 1200px; height: 828px;
    display: flex; align-items: center; justify-content: center; gap: 48px;
  }
  .card {
    position: relative;
    width: 540px; height: 309px;
    overflow: hidden;
    box-shadow: 0 6px 18px rgba(0,0,0,0.18);
  }
  .card-front { background: linear-gradient(160deg, #ffffff 0%, var(--card-white) 55%, #e2e3e5 100%); }
  .card-back { background: var(--charcoal); }
  .card-art { position: absolute; inset: 0; width: 100%; height: 100%; }

  .wordmark {
    position: absolute;
    display: flex; align-items: center; gap: 10px;
    color: var(--ink);
    font-weight: 700;
    letter-spacing: 0.04em;
    line-height: 1.05;
  }
  .wordmark-mark { width: 16px; height: 16px; background: var(--accent); flex: none; }
  .card-front .wordmark { left: 44px; bottom: 58px; font-size: 26px; }
  .card-back .wordmark { right: 34px; bottom: 30px; font-size: 20px; color: var(--text-light); }

  .holder {
    position: absolute; right: 34px; top: 30px;
    text-align: right; color: var(--text-light);
  }
  .holder-name { font-size: 20px; font-weight: 600; letter-spacing: 0.06em; }
  .holder-title { font-size: 13px; letter-spacing: 0.12em; margin-top: 2px; }

  .address {
    position: absolute; right: 34px; top: 102px;
    text-align: right; color: var(--text-light);
    font-size: 12px; line-height: 1.45;
  }
  .contacts {
    position: absolute; right: 34px; top: 150px;
    list-style: none; color: var(--text-light);
    font-size: 9.5px; line-height: 1.75;
  }
  .contacts li { display: flex; justify-content: flex-end; align-items: center; gap: 6px; }
  .contacts svg { width: 9px; height: 9px; fill: none; stroke: var(--text-light); stroke-width: 1.4; }
</style>
</head>
<body>
<main class="canvas">

  <section class="card card-front" aria-label="Card front">
    <svg class="card-art" viewBox="0 0 540 309" preserveAspectRatio="none" aria-hidden="true">
      <defs>
        <linearGradient id="silver" x1="0" y1="0" x2="1" y2="0">
          <stop offset="0" stop-color="#ffffff"/>
          <stop offset="0.5" stop-color="var(--silver-light)"/>
          <stop offset="1" stop-color="#a9abaf"/>
        </linearGradient>
      </defs>
      <path d="M250 0 C300 10 330 60 420 66 C470 70 510 54 540 40 L540 0 Z" fill="url(#silver)"/>
      <path d="M250 0 C305 14 335 64 420 70 C472 73 512 56 540 44" fill="none" stroke="var(--silver-dark)" stroke-width="3"/>
      <path d="M262 0 C312 22 345 78 425 82 C475 84 512 66 540 54" fill="none" stroke="#bfc1c4" stroke-width="1.5"/>
    </svg>
    <div class="wordmark"><span class="wordmark-mark"></span><span>PEARLWOOD<br>FRAMING WORKS</span></div>
  </section>

  <section class="card card-back" aria-label="Card back">
    <svg class="card-art" viewBox="0 0 540 309" preserveAspectRatio="none" aria-hidden="true">
      <defs>
        <linearGradient id="navy" x1="0" y1="0" x2="1" y2="1">
          <stop offset="0" stop-color="var(--navy-deep)"/>
          <stop offset="1" stop-color="var(--navy)"/>
        </linearGradient>
      </defs>
      <path d="M150 0 C250 40 170 230 300 309 L540 309 L540 0 Z" fill="#3a3b44"/>
      <path d="M162 0 C262 40 182 230 312 309 L540 309 L540 0 Z" fill="url(#navy)"/>
    </svg>

    <div class="holder">
      <div class="holder-name">DANA WHITLOCK</div>
      <div class="holder-title">DIRECTOR</div>
    </div>
    <div class="address">7732 Fernglen Pass Ln<br>Austin, TX 78734</div>
    <ul class="contacts">
      <li>(512)555-0193 <svg viewBox="0 0 10 10"><path d="M2 1 L4 1 L4.5 3 L3.3 4 Q4.5 6 6 6.7 L7 5.5 L9 6 L9 8 Q5 9 1.5 4.5 Q1 2.5 2 1 Z"/></svg></li>
      <li>(512)555-0194 <svg viewBox="0 0 10 10"><rect x="2.5" y="0.8" width="5" height="8.4" rx="1"/></svg></li>
      <li>(512)555-0195 <svg viewBox="0 0 10 10"><rect x="1" y="3" width="8" height="5"/><path d="M3 3 V1 H7 V3"/></svg></li>
      <li>hello@pearlwood.example <svg viewBox="0 0 10 10"><rect x="1" y="2" width="8" height="6"/><path d="M1 2 L5 5.5 L9 2"/></svg></li>
      <li>www.pearlwoodframing.example <svg viewBox="0 0 10 10"><circle cx="5" cy="5" r="4"/><path d="M1 5 H9 M5 1 Q2.5 5 5 9 Q7.5 5 5 1"/></svg></li>
    </ul>
    <div class="wordmark"><span class="wordmark-mark"></span><span>PEARLWOOD<br>FRAMING WORKS</span></div>
  </section>

</main>
</body>
</html>
```